Create a cover for English Grammar Workbook

This book describes a system to learn English in a proper way - we call it The ''Lantern Row'' System.

It focuses on not only teaching grammar and its structures, but also giving students tips on how to use it and the best ways to remember what they learn.

The cover should have 3 realistic pillars (3D), with one closer to the front to show that this book is the 1st (front) Pillar.

The title is: "Building Sentences That Stick: *A Friendly Path Through Usage"*

Author's name: Doreen Calloway

```html
<!DOCTYPE html>
<html lang="en">
<head>
<meta charset="UTF-8">
<title>Building Sentences That Stick — Book Cover</title>
<link rel="stylesheet" href="https://fonts.googleapis.com/css2?family=Bebas+Neue&family=Montserrat:wght@600;700&display=swap">
<style>
  :root {
    --backdrop: #3b3b3b;
    --cover-white: #ffffff;
    --ink-dark: #2f2f2f;
    --title-box: #343434;
    --accent-red: #c8191f;
    --pillar-light: #f4f4f4;
    --pillar-mid: #d9d9d9;
  }
  * { margin: 0; padding: 0; box-sizing: border-box; }
  html, body {
    width: 1200px;
    height: 856px;
    overflow: hidden;
    background: var(--backdrop);
  }
  .canvas {
    position: relative;
    width: 1200px;
    height: 856px;
  }
  .cover {
    position: absolute;
    left: 370px;
    top: 98px;
    width: 460px;
    height: 660px;
    background: var(--cover-white);
  }
  .title-lead {
    position: absolute;
    top: 40px;
    left: 0;
    width: 100%;
    text-align: center;
    font-family: "Bebas Neue", "Oswald", sans-serif;
    font-size: 50px;
    letter-spacing: 3px;
    color: var(--ink-dark);
    line-height: 1;
  }
  .title-box {
    position: absolute;
    top: 90px;
    left: 36px;
    width: 418px;
    height: 214px;
    background: var(--title-box);
    border: 7px solid var(--accent-red);
    display: flex;
    flex-direction: column;
    align-items: center;
    justify-content: center;
  }
  .title-main {
    font-family: "Bebas Neue", "Oswald", sans-serif;
    font-size: 104px;
    line-height: 0.92;
    letter-spacing: 2px;
    color: var(--cover-white);
    text-align: center;
  }
  .subtitle {
    position: absolute;
    top: 322px;
    left: 0;
    width: 100%;
    text-align: center;
    font-family: "Montserrat", sans-serif;
    font-weight: 700;
    font-size: 15px;
    letter-spacing: 2.6px;
    color: var(--ink-dark);
  }
  .pillars {
    position: absolute;
    top: 352px;
    left: 70px;
    width: 330px;
    height: 256px;
  }
  .author-band {
    position: absolute;
    top: 612px;
    left: 0;
    width: 100%;
    height: 38px;
    background: var(--accent-red);
    display: flex;
    align-items: center;
    justify-content: center;
    font-family: "Montserrat", sans-serif;
    font-weight: 700;
    font-size: 21px;
    letter-spacing: 4px;
    color: var(--cover-white);
  }
</style>
</head>
<body>
  <main class="canvas">
    <section class="cover">
      <div class="title-lead">BUILDING SENTENCES</div>
      <div class="title-box">
        <div class="title-main">THAT</div>
        <div class="title-main">STICK</div>
      </div>
      <div class="subtitle">A FRIENDLY PATH THROUGH USAGE</div>
      <svg class="pillars" viewBox="0 0 330 256" role="img" aria-label="Three realistic white classical columns, the middle one taller and closer to the front">
        <defs>
          <linearGradient id="pillarTone" x1="0" y1="0" x2="1" y2="0">
            <stop offset="0" stop-color="var(--pillar-mid)"/>
            <stop offset="0.5" stop-color="var(--pillar-light)"/>
            <stop offset="1" stop-color="var(--pillar-mid)"/>
          </linearGradient>
        </defs>
        <rect x="0" y="0" width="330" height="256" fill="url(#pillarTone)" opacity="0.55"/>
      </svg>
      <div class="author-band">DOREEN CALLOWAY</div>
    </section>
  </main>
</body>
</html>
```